Tallwick Home Services Web Site

Design Web site with 3-4 pages: Home, About Us, Services and Order form / Schedule Appointment (which will likely be link to Method App and Quickbooks integration.)
Services include: Dryer Vent Cleaning, AC Cleaning, Difficult-to-Reach Light Bulb replacement, Wood Repair and Home Maintenance Plans including Fire Safety Checks and Filter Replacement.

Target Market(s)

Luxury Home Owners, Professionals (Dr's/lawyers) and Seniors

Industry/Entity Type

Home Maintenance

Coding

Coded - Design and coding required

Requirements
Must have
• Tagline - Where Home Maintenance is Elementary

```html
<!DOCTYPE html>
<html lang="en">
<head>
<meta charset="utf-8">
<title>Tallwick Home Services</title>
<link href="https://fonts.googleapis.com/css2?family=Poppins:wght@400;500;600;700&display=swap" rel="stylesheet">
<style>
:root{
  --gold:#d89c22;
  --ink:#1f1f1f;
  --text:#3a3a3a;
  --paper:#f5f5f5;
  --white:#ffffff;
}
*{box-sizing:border-box;margin:0;padding:0}
html,body{width:1200px;height:4084px;overflow:hidden}
body{position:relative;font-family:"Poppins",sans-serif;color:var(--text);background:var(--paper)}
.abs{position:absolute}
.btn{position:absolute;display:flex;align-items:center;justify-content:center;border-radius:20px;background:var(--gold);color:var(--white);font-weight:600;font-size:12px;white-space:nowrap}
.btn.dark{background:var(--ink)}
.shape{position:absolute}

/* header & hero */
.topline{left:0;top:0;width:1200px;height:5px;background:var(--gold)}
.hero{left:0;top:0;width:1200px;height:730px;background:linear-gradient(180deg,#eceeef 0%,#e3e5e6 60%,#efefef 100%)}
.brand-box{left:143px;top:0;width:153px;height:135px;background:var(--white);display:flex;flex-direction:column;align-items:center;justify-content:center;gap:6px;box-shadow:0 4px 10px rgba(0,0,0,.06)}
.brand-dot{width:22px;height:22px;border-radius:50%;background:var(--gold)}
.brand-name{color:var(--gold);font-weight:600;font-size:13px;text-align:center;line-height:1.25}
.nav{top:60px;font-size:13px;color:var(--ink)}
.nav.active{font-weight:600;border-bottom:2px solid var(--ink);padding-bottom:4px}
.hero-photo{left:140px;top:163px;width:412px;height:412px;border-radius:50%;border:6px solid var(--gold);background:linear-gradient(135deg,#d7dadc,#3a5fa8 55%,#2a2a2a)}
.hero-title{left:596px;top:262px;font-size:50px;font-weight:700;color:var(--ink);letter-spacing:.5px;white-space:nowrap}
.hero-title span{color:var(--gold)}
.hero-copy{left:599px;top:332px;width:450px;font-size:15px;line-height:19px;color:var(--ink)}
.hero-copy strong{font-weight:600}
.dot{position:absolute;width:11px;height:11px;border-radius:50%;background:var(--gold)}
.dot.on{background:var(--ink)}
.dot.ring{background:transparent;border:1.5px solid var(--gold)}

.sec-title{left:0;width:1200px;text-align:center;font-weight:700;color:var(--ink);font-size:36px}

/* services */
.svc-card{width:277px;height:372px;top:851px;background:var(--white);border-radius:16px;box-shadow:0 4px 14px rgba(0,0,0,.07)}
.svc-img{position:absolute;left:10px;top:10px;width:257px;height:190px;border-radius:14px}
.svc-name{position:absolute;left:28px;top:216px;font-size:18px;font-weight:600;color:var(--ink)}
.svc-copy{position:absolute;left:28px;top:246px;width:225px;font-size:11.5px;line-height:15px}
.svc-price{position:absolute;left:28px;top:318px;font-size:16px;font-weight:700;color:var(--ink)}
.svc-card .btn{left:163px;top:312px;width:93px;height:29px;font-size:11px}

/* about */
.about{left:0;top:1366px;width:1200px;height:569px;background:var(--white)}
.about-title{left:176px;top:1458px;font-size:36px;font-weight:700;color:var(--ink)}
.about-title span{color:var(--gold)}
.about-copy{left:176px;top:1514px;width:358px;font-size:11.5px;line-height:18.8px;color:var(--ink)}
.about-photo{left:621px;top:1412px;width:412px;height:412px;border-radius:50%;border:7px solid var(--gold);background:radial-gradient(circle at 50% 60%,#e8e4dc,#9ea2a6 70%)}

/* appointment */
.appt{left:0;top:1934px;width:1200px;height:642px;background:linear-gradient(180deg,#d9a12f,#d69a27)}
.field{position:absolute;border:1.5px solid #6b4d14;border-radius:4px;font-size:18px;color:var(--ink);padding:14px 18px}

/* blog */
.blog-card{top:2733px;width:281px;height:394px;background:var(--white);border-radius:4px;box-shadow:0 4px 14px rgba(0,0,0,.07);overflow:hidden}
.blog-card.hl{background:var(--gold)}
.blog-img{height:199px}
.blog-title{position:absolute;left:24px;top:226px;width:240px;font-size:16px;font-weight:600;color:var(--ink);white-space:nowrap}
.blog-date{position:absolute;left:24px;top:258px;font-size:10px;padding:3px 8px;border:1px solid #ddd;border-radius:3px;background:var(--white);color:var(--text)}
.blog-copy{position:absolute;left:24px;top:287px;width:235px;font-size:10.5px;line-height:15px}
.blog-card.hl .blog-title,.blog-card.hl .blog-copy{color:var(--white)}

/* testimonial */
.testi{left:0;top:3227px;width:1200px;height:470px;background:linear-gradient(180deg,#1b1b1b,#0f0f0f)}
.worker{left:119px;top:3138px;width:357px;height:530px;border-radius:160px 160px 20px 20px;background:linear-gradient(180deg,#2c4c9c,#1f3b84 60%,#16306e)}
.quote-box{left:517px;top:3316px;width:523px;height:171px;border:1.5px dashed #8a8a8a;border-radius:8px}
.avatar{left:474px;top:3354px;width:86px;height:86px;border-radius:50%;border:3px solid var(--white);background:linear-gradient(180deg,#cfc3b3,#8a7a66)}
.quote-text{left:578px;top:3378px;width:430px;font-size:10.5px;line-height:15px;color:var(--white)}

/* footer */
.footer{left:0;top:3600px;width:1200px;height:484px;background:var(--gold)}
.f-head{top:3748px;font-size:16px;font-weight:600;color:var(--ink)}
.f-txt{font-size:11px;color:var(--ink);line-height:14px}
.social{position:absolute;width:32px;height:32px;border-radius:50%;border:1.5px solid var(--white)}
.social.fill{background:var(--ink);border-color:var(--ink)}
.foot-brand{left:780px;top:3790px;width:260px;text-align:center;font-size:30px;font-weight:600;color:var(--ink);line-height:1.2}
.copyright{left:0;top:3999px;width:1200px;text-align:center;font-size:10px;color:var(--ink)}
</style>
</head>
<body>

<!-- Hero -->
<div class="abs hero"></div>
<div class="abs topline"></div>
<div class="abs brand-box"><div class="brand-dot"></div><div class="brand-name">Tallwick<br>Home Services</div></div>
<div class="abs nav active" style="left:470px">Home</div>
<div class="abs nav" style="left:535px">About Us</div>
<div class="abs nav" style="left:620px">Services</div>
<div class="abs nav" style="left:702px">Contact Us</div>
<div class="btn" style="left:805px;top:55px;width:211px;height:32px">Schedule an Appointment</div>
<div class="abs hero-photo" role="img" aria-label="Technician in cap servicing a wall air conditioner"></div>
<div class="abs hero-title">TALLWICK <span>HOMES</span></div>
<div class="abs hero-copy"><strong>Where Home Maintenance is Elementary.</strong> Lorem ipsum dolor sit amet, consectetur adipiscing elit, sed do eiusmod tempor incididunt ut labore.</div>
<div class="btn" style="left:599px;top:402px;width:203px;height:31px">Schedule an Appointment</div>
<div class="dot" style="left:594px;top:545px"></div>
<div class="dot on" style="left:614px;top:545px"></div>
<div class="dot" style="left:634px;top:545px"></div>
<div class="dot" style="left:654px;top:545px"></div>
<svg class="shape" style="left:0;top:620px" width="1200" height="115" viewBox="0 0 1200 115">
  <path d="M0 115 C200 40 420 10 620 40 C800 65 950 90 1200 30 L1200 115 Z" fill="var(--paper)"/>
  <path d="M0 110 C180 30 420 0 620 30 C800 58 960 80 1200 20 C980 95 800 70 620 52 C420 30 200 40 0 115 Z" fill="var(--gold)"/>
</svg>

<!-- Services -->
<div class="abs sec-title" style="top:780px">SERVICES</div>
<div class="abs svc-card" style="left:158px">
  <div class="svc-img" role="img" aria-label="Technician spraying cleaner into an AC unit" style="background:linear-gradient(135deg,#e8eef2,#9fb6cc)"></div>
  <div class="svc-name">AC Cleaning</div>
  <div class="svc-copy">Coil and filter cleaning for cooler air, lower bills and a longer-lasting unit, with filter replacement included.</div>
  <div class="svc-price">$345</div><div class="btn">Book Now</div>
</div>
<div class="abs svc-card" style="left:461px">
  <div class="svc-img" role="img" aria-label="Flashlight inspecting a metal dryer vent duct" style="background:linear-gradient(135deg,#5a4530,#1e1a16)"></div>
  <div class="svc-name">Dryer Vent Cleaning</div>
  <div class="svc-copy">Lint removal and airflow check from dryer to outside vent, paired with a fire safety check of the laundry area.</div>
  <div class="svc-price">$345</div><div class="btn">Book Now</div>
</div>
<div class="abs svc-card" style="left:764px">
  <div class="svc-img" role="img" aria-label="Carpenter in hard hat repairing wood siding" style="background:linear-gradient(135deg,#a97c4e,#5c4a3e)"></div>
  <div class="svc-name">Wood Repair</div>
  <div class="svc-copy">Careful repair of siding, trim and decking, plus difficult-to-reach light bulb replacement on the same visit.</div>
  <div class="svc-price">$345</div><div class="btn">Book Now</div>
</div>
<div class="dot" style="left:556px;top:1282px;width:9px;height:9px"></div>
<div class="dot ring" style="left:576px;top:1282px;width:9px;height:9px"></div>
<div class="dot" style="left:596px;top:1282px;width:9px;height:9px"></div>
<div class="dot" style="left:616px;top:1282px;width:9px;height:9px"></div>
<div class="dot" style="left:636px;top:1282px;width:9px;height:9px"></div>

<!-- About -->
<div class="abs about"></div>
<div class="abs about-title">ABOUT <span>US</span></div>
<div class="abs about-copy">Lorem ipsum dolor sit amet, consectetur adipiscing elit, sed do eiusmod tempor incididunt ut labore et dolore magna aliqua. Quis ipsum suspendisse ultrices gravida. Risus commodo viverra maecenas accumsan lacus vel facilisis. Lorem ipsum dolor sit amet, consectetur adipiscing elit, sed do eiusmod tempor incididunt ut labore et dolore magna aliqua. Quis ipsum suspendisse ultrices gravida. Risus commodo viverra maecenas accumsan lacus vel facilisis. Lorem ipsum dolor sit amet, consectetur adipiscing elit, sed do eiusmod tempor incididunt ut labore et dolore magna aliqua. Quis ipsum suspendisse ultrices gravida. Risus commodo viverra maecenas accumsan lacus vel facilisis.</div>
<div class="btn" style="left:174px;top:1760px;width:92px;height:28px;font-size:11px">Read more</div>
<div class="abs about-photo" role="img" aria-label="Model house on coins surrounded by hands holding tools"></div>

<!-- Appointment -->
<div class="abs appt" role="img" aria-label="Smiling technician with clipboard under a gold overlay"></div>
<div class="abs sec-title" style="top:2016px;font-size:34px">SCHEDULE AN APPOINTMENT</div>
<div class="field" style="left:184px;top:2111px;width:268px;height:53px">Name</div>
<div class="field" style="left:465px;top:2111px;width:270px;height:53px">Email</div>
<div class="field" style="left:747px;top:2111px;width:270px;height:53px">Phone</div>
<div class="field" style="left:184px;top:2184px;width:833px;height:53px">Services</div>
<div class="field" style="left:184px;top:2254px;width:833px;height:115px">Message</div>
<div class="btn dark" style="left:510px;top:2392px;width:179px;height:32px">Book an Appointment</div>
<svg class="shape" style="left:0;top:2465px" width="1200" height="115" viewBox="0 0 1200 115">
  <path d="M0 115 C220 30 430 20 620 50 C820 80 1000 85 1200 20 L1200 115 Z" fill="var(--paper)"/>
  <path d="M0 100 C200 20 430 10 620 40 C820 72 1000 70 1200 10 C1010 95 820 95 620 68 C430 42 220 40 0 115 Z" fill="var(--gold)"/>
</svg>

<!-- Blog -->
<div class="abs sec-title" style="top:2652px">BLOG</div>
<div class="abs blog-card" style="left:158px">
  <div class="blog-img" role="img" aria-label="Worker fitting a kitchen countertop" style="background:linear-gradient(135deg,#c9b8a4,#5a5048)"></div>
  <div class="blog-title">CARING FOR WOODWORK</div><div class="blog-date">2025-02-04</div>
  <div class="blog-copy">Lorem ipsum dolor sit amet, consectetur adipiscing elit, sed do eiusmod tempor incididunt ut labore et dolore magna aliqua. Quis ipsum suspendisse ultrices gravida. Risus commodo viverra maecenas accumsan</div>
</div>
<div class="abs blog-card hl" style="left:459px">
  <div class="blog-img" role="img" aria-label="Technician handling attic ductwork" style="background:linear-gradient(135deg,#8a6a48,#2e2a28)"></div>
  <div class="btn" style="left:80px;top:80px;width:120px;height:34px;font-size:10px;border-radius:18px">LEARN MORE</div>
  <div class="blog-title">MAINTENANCE PLANS</div><div class="blog-date">2025-02-04</div>
  <div class="blog-copy">Home Maintenance Plans bundle regular fire safety checks and filter replacement into one simple schedule. Lorem ipsum dolor sit amet, consectetur adipiscing elit, sed do eiusmod tempor.</div>
</div>
<div class="abs blog-card" style="left:759px">
  <div class="blog-img" role="img" aria-label="Hand changing a bulb in a pendant light" style="background:linear-gradient(135deg,#efe6da,#b08a5c)"></div>
  <div class="blog-title">HARD-TO-REACH BULBS</div><div class="blog-date">2025-02-04</div>
  <div class="blog-copy">Difficult-to-reach light bulb replacement for high ceilings, stairwells and chandeliers, done safely with the right ladder. Lorem ipsum dolor sit amet, consectetur adipiscing elit.</div>
</div>

<!-- Testimonial -->
<div class="abs testi" role="img" aria-label="Dimmed kitchen background"></div>
<div class="abs footer"></div>
<svg class="shape" style="left:0;top:3590px" width="1200" height="110" viewBox="0 0 1200 110">
  <path d="M0 0 L1200 0 L1200 10 C1000 80 700 20 420 50 C250 70 120 90 0 80 Z" fill="#121212"/>
</svg>
<div class="abs worker" role="img" aria-label="Smiling technician in blue uniform with arms crossed"></div>
<div class="abs quote-box"></div>
<div class="abs avatar" role="img" aria-label="Customer portrait"></div>
<div class="abs" style="left:574px;top:3340px;font-size:40px;font-weight:700;color:var(--white);line-height:1">&ldquo;</div>
<div class="abs quote-text">Lorem ipsum dolor sit amet, consectetur adipiscing elit, sed do eiusmod tempor incididunt ut labore et dolore magna aliqua. Quis ipsum suspendisse ultrices gravida. Risus commodo viverra maecenas accumsan lacus vel facilisis.</div>
<div class="abs" style="left:580px;top:3430px;font-size:16px;font-weight:600;color:var(--white)">-Marla</div>
<div class="dot" style="left:960px;top:3509px;width:9px;height:9px;background:var(--white)"></div>
<div class="dot" style="left:979px;top:3509px;width:9px;height:9px;background:var(--white)"></div>
<div class="dot" style="left:998px;top:3509px;width:9px;height:9px"></div>

<!-- Footer -->
<div class="abs f-head" style="left:160px">Contact Us</div>
<svg class="shape" style="left:162px;top:3791px" width="12" height="16" viewBox="0 0 12 16"><path d="M6 0a6 6 0 0 0-6 6c0 4.5 6 10 6 10s6-5.5 6-10a6 6 0 0 0-6-6zm0 8.5A2.5 2.5 0 1 1 6 3.5a2.5 2.5 0 0 1 0 5z" fill="var(--ink)"/></svg>
<div class="abs f-txt" style="left:187px;top:3787px;width:120px;line-height:12px">#123, Lorium ipsum Dolor amit, City.</div>
<svg class="shape" style="left:162px;top:3848px" width="14" height="14" viewBox="0 0 24 24"><path d="M6.6 10.8a15 15 0 0 0 6.6 6.6l2.2-2.2a1 1 0 0 1 1-.25 11.4 11.4 0 0 0 3.6.57 1 1 0 0 1 1 1V20a1 1 0 0 1-1 1A17 17 0 0 1 3 4a1 1 0 0 1 1-1h3.5a1 1 0 0 1 1 1c0 1.25.2 2.45.57 3.57a1 1 0 0 1-.25 1z" fill="var(--ink)"/></svg>
<div class="abs f-txt" style="left:187px;top:3848px">1-555-010-2040</div>
<svg class="shape" style="left:162px;top:3880px" width="14" height="11" viewBox="0 0 14 11"><rect width="14" height="11" rx="1" fill="var(--ink)"/><path d="M1 1l6 5 6-5" stroke="var(--gold)" fill="none" stroke-width="1.3"/></svg>
<div class="abs f-txt" style="left:187px;top:3877px">info@tallwick.co</div>

<div class="abs f-head" style="left:368px">Quick Links</div>
<div class="abs f-txt" style="left:368px;top:3786px;line-height:19px;font-size:10px">&rsaquo;&nbsp;&nbsp;&nbsp;Home<br>&rsaquo;&nbsp;&nbsp;&nbsp;About Us<br>&rsaquo;&nbsp;&nbsp;&nbsp;Services<br>&rsaquo;&nbsp;&nbsp;&nbsp;Blog<br>&rsaquo;&nbsp;&nbsp;&nbsp;Contact Us<br>&rsaquo;&nbsp;&nbsp;&nbsp;FAQ</div>

<div class="abs f-head" style="left:555px">Newsletter</div>
<div class="abs" style="left:555px;top:3792px;width:196px;height:25px;background:var(--white);font-size:9px;color:var(--ink);padding:6px 12px">Enter Your email</div>
<svg class="shape" style="left:727px;top:3799px" width="12" height="12" viewBox="0 0 12 12"><path d="M0 6L12 0 9 12 6 7z" fill="var(--ink)"/></svg>
<div class="social fill" style="left:556px;top:3855px"></div>
<div class="social" style="left:599px;top:3855px"></div>
<div class="social" style="left:643px;top:3855px"></div>
<div class="social" style="left:688px;top:3855px"></div>

<div class="abs foot-brand">Tallwick<br>Home Services</div>

<div class="abs copyright">Copyright &copy; 2025 &bull; www.tallwickhomes.com &bull; All Rights Reserved &nbsp;|&nbsp; Privacy Policy &amp; Terms of use</div>
<div class="abs" style="left:1033px;top:4000px;width:30px;height:30px;border-radius:50%;background:#2fb34a"></div>

</body>
</html>
```